Lotstallmart.com Webpage Design

Design Brief for lotstallmart.com (Copy of Brief also in attached Word file)

Name of Website- lotstallmart.com (existing logo and look & feel of website to be changed)

Logo - Finalised. The logo files are attached with the brief as “logo.jpeg”. The “Blue- Grey” version of the logo is for use on lighter backgrounds and the “Orange-White” version of the logo is for use on darker backgrounds. (A full Black version of the logo is also attached). Both versions may be used in different parts of the website. All attached files are in .png format.
Status - The website in functional and is undergoing user trials. However, we want to improve the look & feel of the website so at it seems
a. cotemporary,
b. Easy to Navigate
c. professional and
d. Vibrant.

Please visit ‘lotstallmart.com’ to check out the website and its functionalities – please use it only as a reference for the features & functions to be provided, however the designer should use a ‘Free Hand’ in designing the composition of various parts of the webpage without getting too influenced by the existing design

Objective of the Website ‘lotstallmart.com –
a. It is a portal focussed on listing of ‘Retail’ specific real-estate properties by developers, owners and realty brokers. The properties shall listed under the following four categories-
i. Retail Malls
ii. Shopping Complexes
iii. High-street shops
iv. Retail Warehouses
*refer lotstallmart.com for better clarity

b. The abovementioned properties shall be listed either for ‘Sale’ or ‘rent\lease’ or both

c. Users shall visit the site in case they wish to acquire a retail \ shop space either on ‘sale’ or ‘rent’. These Users would be able to specify the ‘Search Criteria’ through the tool-bars provided on the website – the ‘Search Criteria’ shall comprise of ‘Type of space category’, ‘City’, ‘Locality’, transaction type ie ‘Rent \ Sale’ and ‘Area Range’

d. The main revenue model for the website shall be listing fee ( or advertising charges ) payable by those listing their properties on the website.

Three Main Pages of Website (lotstallmart.com) that need to be designed -
a. Main Home Page (visit the web link - http://lotstallmart.com/ ) - The main home page has the “Search Toolbar” for specifying of Search Criteria by the User. It shall also have the following features & functions-
i. Main Advertising Banner
ii. Featured Projects
iii. New Launches
iv. Toolbar with buttons – ‘Advertise with Us’, ‘Listings Alert’, ‘Mart Wizards’, ‘Advertiser Login’

b. Property Listings Page (visit the web link - http://lotstallmart.com/gurgaon-in-india ) - The List of property options that match the Criteria specified by the ‘User’ get displayed on this page.

c. Property Detail Page - When the ‘User’ clicks on the “More….” Button on the ‘Property Listings Page’ (given in point b. above) the web page with the details of the property opens. (For Example – visit the web link - http://lotstallmart.com/vorne-Shopping-Complex-vorne-quadrion-gurgaon-636 )

Note:- Please refer to attached ‘Shopping’ related images the designer may use them on the website to provide a look & feel of retail if required – either separately or rotate in a single window

Target Market(s)

Retailers & Investors looking for retail space, Real Estate Brokers, Developers

Industry/Entity Type

Advertising

Number of Pages Required

3 page

Requirements
Must have
• Refer to existing site lotstallmart.com -- all the existing functionalities are a must have.
Nice to have
• The Designer may use the retail related images on the website if required for making it more vibrant. Refer attached images Shopping(1-6).jpg

```html
<!DOCTYPE html>
<html lang="en">
<head>
<meta charset="utf-8">
<title>Lotstallmart.com – Retail Spaces Across India</title>
<link href="https://fonts.googleapis.com/css2?family=Open+Sans:wght@400;600;700;800&display=swap" rel="stylesheet">
<style>
:root{
  --blue:#1e90e6;
  --blue-dark:#1577c2;
  --ink:#222;
  --text:#444;
  --muted:#888;
  --line:#ddd;
  --topbar:#1f1f1f;
  --panel:#2e2e2e;
  --panel-2:#3b3b3b;
  --footer:#262626;
  --footer-bottom:#1a1a1a;
  --white:#fff;
  --orange:#f39a1e;
}
*{box-sizing:border-box;margin:0;padding:0}
html,body{width:1200px;height:2488px;overflow:hidden}
body{font-family:"Open Sans",Arial,sans-serif;color:var(--text);background:var(--white);font-size:14px}
.wrap{width:1040px;margin:0 auto;position:relative}

/* top city bar */
.city-bar{height:36px;background:var(--topbar);display:flex;justify-content:center;align-items:center;gap:22px}
.city-bar a{color:#ccc;font-size:12px;text-decoration:none}

/* header */
.site-header{height:72px;display:flex;align-items:center}
.site-header .wrap{display:flex;align-items:center;justify-content:space-between}
.brand{display:flex;align-items:center;gap:10px;color:#4a6077;font-weight:800;font-size:28px}
.brand-dot{width:22px;height:22px;border-radius:50%;background:var(--blue)}
.brand-tag{font-size:9px;color:var(--muted);font-weight:400;display:block;letter-spacing:.5px}
.header-links{display:flex;gap:40px;align-items:center}
.header-link{font-size:13px;color:var(--blue);font-weight:700;line-height:1.2}
.header-link small{display:block;color:var(--muted);font-weight:400;font-size:10px}
.login-box{text-align:right;font-size:11px;color:var(--muted)}
.login-btn{display:inline-block;margin:4px 0;background:var(--blue);color:var(--white);font-weight:700;font-size:13px;padding:6px 16px;border-radius:3px}
.login-box .register{color:var(--blue)}

/* hero */
.hero{position:relative;height:712px}
.hero-photo{position:absolute;inset:0;background:linear-gradient(120deg,#8a6a52 0%,#c9a78a 30%,#e9d8c6 55%,#b55a45 78%,#6b4f5f 100%)}
.search-tabs{position:absolute;left:80px;right:80px;top:500px;height:50px;background:rgba(255,255,255,.95);display:flex}
.search-tab{flex:1;display:flex;align-items:center;gap:12px;padding-left:26px;font-size:15px;color:var(--ink);font-weight:600;border-right:1px solid var(--line)}
.search-tab:last-child{border-right:0}
.tab-icon{width:26px;height:22px;border:2px solid #555;border-radius:2px}
.search-panel{position:absolute;left:80px;right:80px;top:550px;height:150px;background:rgba(30,30,30,.9);display:flex;padding:22px 26px;gap:24px;color:var(--white)}
.format h3{font-size:16px;font-weight:700;margin-bottom:12px}
.format ul{list-style:none;display:grid;grid-template-columns:110px 120px;gap:8px;font-size:11px}
.format li::before{content:"";display:inline-block;width:10px;height:10px;background:var(--white);margin-right:6px;vertical-align:-1px}
.fields{flex:1;display:grid;grid-template-columns:1fr 1fr 150px;gap:8px 12px;align-content:start}
.field label{display:block;font-size:11px;color:#ccc;margin-bottom:3px}
.field .select{height:26px;background:var(--white);color:#555;font-size:11px;padding:5px 8px;position:relative}
.field .select::after{content:"";position:absolute;right:8px;top:10px;border:5px solid transparent;border-top-color:#555}
.split{display:grid;grid-template-columns:1fr 1fr;gap:8px}
.search-btn{grid-column:3;grid-row:2 / span 2;align-self:end;background:var(--blue);color:var(--white);font-weight:700;text-align:center;height:30px;line-height:30px;font-size:14px}

/* listings */
.listings{padding:44px 0 30px}
.listings + .listings{border-top:1px solid var(--line)}
.section-head{display:flex;justify-content:space-between;align-items:center;margin-bottom:26px}
.section-title{font-size:34px;font-weight:700;color:var(--ink)}
.section-title span{font-size:22px;color:var(--muted);font-weight:400}
.arrows{display:flex;gap:6px}
.arrow{width:22px;height:22px;border-radius:50%;background:#333;display:flex;align-items:center;justify-content:center}
.cards{display:grid;grid-template-columns:repeat(4,1fr);gap:40px}
.card{text-align:center}
.card-photo{height:180px;margin-bottom:12px}
.card-name{font-size:16px;color:var(--blue);font-weight:700}
.card-place{font-size:13px;color:var(--ink);font-weight:600}
.card-type{font-size:11px;color:var(--muted);text-transform:uppercase;margin-bottom:10px}
.card-btn{display:block;background:var(--blue);color:var(--white);font-size:12px;font-weight:700;padding:7px 0}
.ph-a{background:linear-gradient(135deg,#b7c7d6,#e1d3bf)}
.ph-b{background:linear-gradient(135deg,#c79c6f,#8d6d57)}
.ph-c{background:linear-gradient(135deg,#d3b295,#6c86a3)}
.ph-d{background:linear-gradient(135deg,#a9b4bd,#ececec)}

/* alert + wizards */
.engage{display:flex;height:368px;margin-top:8px}
.engage-col{flex:1;padding:30px 60px 0 108px}
.engage-col.right{padding-left:40px;padding-right:108px}
.alert{background:var(--panel)}
.wizards{background:var(--blue)}
.engage h2{font-size:24px;color:var(--white);font-weight:600;margin-bottom:14px}
.engage p{font-size:12px;color:#e6e6e6;line-height:1.5;margin-bottom:14px}
.mail-row{display:flex;gap:14px;align-items:center;margin-bottom:14px}
.mail-icon{width:36px;height:36px;border-radius:50%;background:var(--blue);display:flex;align-items:center;justify-content:center}
.input{height:28px;background:var(--white);margin-bottom:8px;font-size:11px;color:#999;padding:6px 10px}
.input.dark{background:#555;color:#ddd}
.input.tall{height:50px}
.hint{font-size:10px;color:#aaa;margin:-4px 0 8px}
.submit{display:inline-block;font-size:11px;color:var(--white);padding:6px 16px;background:var(--blue);margin-top:4px}
.wizards .submit{background:var(--white);color:var(--blue)}

/* footer */
.site-footer{background:var(--footer);height:168px;color:#bbb;font-size:11px}
.site-footer .wrap{display:grid;grid-template-columns:1.3fr 1.4fr 1fr;padding-top:22px;gap:30px}
.site-footer h4{color:var(--white);font-size:13px;margin-bottom:10px}
.foot-links{display:grid;grid-template-columns:1fr 1fr;gap:3px 20px}
.site-footer p{line-height:1.5}
.footer-bottom{background:var(--footer-bottom);height:40px;color:#888;font-size:11px}
.footer-bottom .wrap{display:flex;justify-content:space-between;line-height:40px}
</style>
</head>
<body>

<nav class="city-bar">
  <a>Bangalore</a><a>Chennai</a><a>Greater Noida</a><a>Gurgaon</a><a>Hyderabad</a><a>Jaipur</a><a>Kharar</a><a>Kolkata</a><a>Mumbai</a><a>Noida</a><a>Pune</a><a>Surat</a>
</nav>

<header class="site-header">
  <div class="wrap">
    <div class="brand"><span class="brand-dot"></span><span>lotstallmart<span class="brand-tag">RETAIL PROPERTIES ACROSS INDIA</span></span></div>
    <div class="header-links">
      <div class="header-link">Advertise with us<small>Get listed today</small></div>
      <div class="header-link">Mart Wizards<small>Retail space experts</small></div>
      <div class="header-link">Listing Alert<small>Stay updated</small></div>
      <div class="login-box">Get your property listed<br><span class="login-btn">Advertiser Login</span><br><span class="register">New Advertiser – Register</span></div>
    </div>
  </div>
</header>

<section class="hero">
  <div class="hero-photo" role="img" aria-label="Shoppers carrying bags walking through a bright retail mall"></div>
  <div class="search-tabs">
    <div class="search-tab"><span class="tab-icon"></span>Retail Malls</div>
    <div class="search-tab"><span class="tab-icon"></span>Shopping Complex</div>
    <div class="search-tab"><span class="tab-icon"></span>High Street Shops</div>
    <div class="search-tab"><span class="tab-icon"></span>Retail Warehouse</div>
  </div>
  <form class="search-panel">
    <div class="format">
      <h3>SELECT RETAIL FORMAT</h3>
      <ul>
        <li>Retail Malls</li><li>Shopping Complex</li>
        <li>High Street</li><li>Retail Warehouse</li>
      </ul>
    </div>
    <div class="fields">
      <div class="field"><label>Sale or Rent Or Both</label><div class="select">Both</div></div>
      <div class="field"><label>Select City</label><div class="select">Select</div></div>
      <div></div>
      <div class="field"><label>Select Locality/Micro-Market</label><div class="select">Select</div></div>
      <div class="field"><label>Area Range</label><div class="split"><div class="select">Min</div><div class="select">Max</div></div></div>
      <div class="search-btn">SEARCH</div>
    </div>
  </form>
</section>

<section class="listings">
  <div class="wrap">
    <div class="section-head">
      <h2 class="section-title">Featured Retail Projects <span>Across India</span></h2>
      <div class="arrows">
        <span class="arrow"><svg width="8" height="10"><path d="M6 1 2 5l4 4" stroke="#fff" stroke-width="2" fill="none"/></svg></span>
        <span class="arrow"><svg width="8" height="10"><path d="M2 1l4 4-4 4" stroke="#fff" stroke-width="2" fill="none"/></svg></span>
      </div>
    </div>
    <div class="cards">
      <article class="card"><div class="card-photo ph-a" role="img" aria-label="Mall interior with shoppers"></div><div class="card-name">Corvane</div><div class="card-place">Althan</div><div class="card-type">Shopping Complex</div><a class="card-btn">VIEW THE LISTING</a></article>
      <article class="card"><div class="card-photo ph-b" role="img" aria-label="Shoppers at a high street store"></div><div class="card-name">Keel 81 High Street</div><div class="card-place">Sector 81</div><div class="card-type">Shopping Complex</div><a class="card-btn">VIEW THE LISTING</a></article>
      <article class="card"><div class="card-photo ph-c" role="img" aria-label="Retail shopping arcade"></div><div class="card-name">Tavro Cosmopolitan</div><div class="card-place">Sector 66</div><div class="card-type">Shopping Complex</div><a class="card-btn">VIEW THE LISTING</a></article>
      <article class="card"><div class="card-photo ph-d" role="img" aria-label="Modern shopping mall atrium"></div><div class="card-name">Zenor 24B</div><div class="card-place">Sohna Road</div><div class="card-type">Shopping Complex</div><a class="card-btn">VIEW THE LISTING</a></article>
    </div>
  </div>
</section>

<section class="listings">
  <div class="wrap">
    <div class="section-head">
      <h2 class="section-title">Featured New Launches <span>Across India</span></h2>
      <div class="arrows">
        <span class="arrow"><svg width="8" height="10"><path d="M6 1 2 5l4 4" stroke="#fff" stroke-width="2" fill="none"/></svg></span>
        <span class="arrow"><svg width="8" height="10"><path d="M2 1l4 4-4 4" stroke="#fff" stroke-width="2" fill="none"/></svg></span>
      </div>
    </div>
    <div class="cards">
      <article class="card"><div class="card-photo ph-b" role="img" aria-label="Large retail mall exterior"></div><div class="card-name">The Grand Arcade Place</div><div class="card-place">Andar Road</div><div class="card-type">Retail Malls</div><a class="card-btn">VIEW THE LISTING</a></article>
      <article class="card"><div class="card-photo ph-d" role="img" aria-label="Shopping centre corridor"></div><div class="card-name">Crest One</div><div class="card-place">Sector 18</div><div class="card-type">Shopping Complex</div><a class="card-btn">VIEW THE LISTING</a></article>
      <article class="card"><div class="card-photo ph-a" role="img" aria-label="Shoppers in a mall"></div><div class="card-name">Urban Core - SCO In Sector</div><div class="card-place">Sihon Majra</div><div class="card-type">Shopping Complex</div><a class="card-btn">VIEW THE LISTING</a></article>
      <article class="card"><div class="card-photo ph-c" role="img" aria-label="Retail store fronts"></div><div class="card-name">SCO In Sector 117 On</div><div class="card-place">Sihon Majra</div><div class="card-type">Shopping Complex</div><a class="card-btn">VIEW THE LISTING</a></article>
    </div>
  </div>
</section>

<section class="engage">
  <div class="engage-col alert">
    <h2>Listing Alert</h2>
    <div class="mail-row">
      <span class="mail-icon"><svg width="18" height="13"><rect x="1" y="1" width="16" height="11" fill="none" stroke="#fff" stroke-width="1.5"/><path d="M1 1l8 6 8-6" fill="none" stroke="#fff" stroke-width="1.5"/></svg></span>
      <p style="margin:0">Subscribe for fortnightly email<br>updates on new listings at Lotstallmart</p>
    </div>
    <div class="input">Enter your email address</div>
    <div class="input dark">Select options</div>
    <div class="hint">(select one or more formats)</div>
    <div class="input dark">Select city</div>
    <div class="hint">(select one or more cities)</div>
    <span class="submit">Subscribe Now</span>
  </div>
  <div class="engage-col right wizards">
    <h2>Mart Wizards</h2>
    <p>Our retail space experts help you find the right shop, mall unit or warehouse. Share your needs below and our team will call you back soon.</p>
    <div class="input">Enter your name</div>
    <div class="input">Enter your email</div>
    <div class="input">Enter your mobile number</div>
    <div class="input tall">Add description of requirement</div>
    <span class="submit">Submit Now</span>
  </div>
</section>

<footer class="site-footer">
  <div class="wrap">
    <div>
      <h4>About Mart Central</h4>
      <div class="foot-links">
        <span>About Us</span><span>Retail Malls</span>
        <span>Privacy Policy</span><span>Shopping Complex</span>
        <span>Terms of Use</span><span>High Street Shops</span>
        <span>Contact Us</span><span>Retail Warehouses</span>
        <span>Site Map</span><span></span>
      </div>
    </div>
    <div>
      <h4>www.lotstallmart.com</h4>
      <p>India's dedicated portal for retail real estate. Browse malls, shopping complexes, high street shops and retail warehouses listed by developers, owners and brokers for sale or rent across major cities.</p>
    </div>
    <div>
      <h4>Contact</h4>
      <p>Mart Central<br>12 Sample Street, Block C<br>Sector 44, Gurgaon<br>Phone : +91 000 555 0182<br>Fax : +91 000 555 0183</p>
    </div>
  </div>
</footer>
<div class="footer-bottom">
  <div class="wrap"><span>Copyright © 2015 lotstallmart.com. All rights reserved.</span><span>Terms &amp; Condition | Privacy Policy</span></div>
</div>

</body>
</html>
```